A 'new law' boutique Australian law firm that provides specialist employment law and people managem

We value helping clients create results with respect workplaces. What differentiates us is we provide actionable training in understanding and dealing with people and ensure legal compliance fits with this approach. We would like a fresh approach to our training overview documents that we currently use in our current law firm (6 attached). Please use pictures, symbols etc consistent with our non-traditional law approach that captures the approach of each training session.. Attached is the logo and draft letterhead for Birchwell Legal which will launch soon.

Target Market(s)

HR Managers and in-house lawyers (non employment specialists) in mid-large Australian companies that are progressive with a relationship based approach to managing employee behaviours and disputes.

Industry/Entity Type

Human Resource

Font styles to use
Sans Serif

Colors
3176b5
33a6d7

Requirements
Must have
• 1 or 2 page PDF for each of the 6 documents that the wording supplied goes into your design which will be pretty similar as we want consistency with our documents

```html
<!DOCTYPE html>
<html lang="en">
<head>
<meta charset="utf-8">
<title>Contact Officer Training – Birchwell Legal</title>
<link href="https://fonts.googleapis.com/css2?family=Bitter:ital,wght@0,300;0,400;0,500;0,600;1,400;1,500&display=swap" rel="stylesheet">
<style>
  :root{
    --ink-dark:#2e2e30;
    --brand-blue:#3176b5;
    --sky:#33a6d7;
    --band-strong:#45bbeb;
    --band-mid:#8fd2f3;
    --band-soft:#dcf0fb;
    --heading-grey:#333334;
    --text-grey:#2b2b2b;
    --white:#ffffff;
    --ring-grey:#7b7b7d;
  }
  *{box-sizing:border-box;margin:0;padding:0}
  html,body{width:848px;height:1200px;overflow:hidden;background:var(--white)}
  body{font-family:"Bitter",Georgia,serif;color:var(--text-grey);position:relative}
  .sheet{position:relative;width:848px;height:1200px}

  /* left column */
  .intro{position:absolute;left:0;top:0;width:505px;height:824px;background:var(--ink-dark);color:var(--white)}
  .brand{position:absolute;right:48px;top:92px;text-align:right}
  .brand-name{display:flex;align-items:center;gap:10px;justify-content:flex-end;font-size:29px;font-weight:500;color:var(--sky);letter-spacing:.5px}
  .brand-dot{width:16px;height:16px;border-radius:50%;background:var(--white)}
  .brand-tag{font-size:9.5px;font-weight:500;letter-spacing:.4px;margin-top:3px}
  .title{position:absolute;right:49px;top:210px;text-align:right;font-weight:500;font-size:37px;line-height:43px}
  .title .accent{color:var(--sky)}
  .need-heading{position:absolute;right:49px;top:313px;color:var(--sky);font-size:21px;font-weight:500}
  .need-body{position:absolute;right:49px;top:356px;width:420px;text-align:right;font-size:12.6px;font-weight:300;line-height:19.5px}
  .need-body p{margin-bottom:16px}

  .icon-badge{position:absolute;left:79px;top:753px;width:142px;height:142px}

  .outcomes{position:absolute;left:60px;top:898px;width:410px}
  .outcomes h2{color:var(--brand-blue);font-size:21px;font-weight:500;margin-bottom:12px}
  .outcomes .lead{font-size:12.6px;font-weight:500;line-height:17px;margin-bottom:7px}
  .outcomes ol{list-style:none;font-size:12.6px;font-weight:300;line-height:17px}
  .outcomes li{margin-bottom:8.5px;padding-left:12px;text-indent:-12px}

  /* right column */
  .overview{position:absolute;left:505px;top:0;width:343px;height:1200px}
  .band{position:absolute;left:0;width:343px;padding-left:41px;padding-right:14px}
  .band.strong{background:var(--band-strong)}
  .band.mid{background:var(--band-mid)}
  .band.soft{background:var(--band-soft)}
  .band h3{color:var(--heading-grey);font-size:17.5px;font-weight:500;margin-bottom:6px}
  .band p{font-size:12.6px;line-height:16.5px;color:var(--white);margin-bottom:4.5px}
  .band p.bold{font-weight:500}
  .band p.ex{font-style:italic;font-weight:500}
  .band.soft p{color:var(--text-grey)}
  .band.small p{font-size:11px;line-height:16.5px}
  .overview-title{color:var(--brand-blue);font-size:21px;font-weight:500;margin-left:-3px;margin-bottom:2px}
  .band.strong .ex, .band.mid .ex{color:var(--white)}
  .band.mid .ex.dark{color:var(--heading-grey)}
</style>
</head>
<body>
<main class="sheet">

  <section class="intro">
    <div class="brand">
      <div class="brand-name"><span class="brand-dot"></span>Birchwell Legal</div>
      <div class="brand-tag">INTEGRATED WORKPLACE SPECIALISTS</div>
    </div>
    <h1 class="title">Contact<br><span class="accent">Officer Training</span></h1>
    <h2 class="need-heading">Training Need</h2>
    <div class="need-body">
      <p>Unlawful or inappropriate behavior in the workplace that is left unaddressed can impact on productivity and employee retention. Claims can be costly in terms of time and money as well as the impact on mental health from being involved in uncomfortable adversarial processes.</p>
      <p>Clear policies and procedures explaining the organisation’s workplace behavior expectations and how grievances will be managed are a minimum compliance requirement.</p>
      <p>The challenge is ensuring that employees understand the directions contained in those policies, what is unlawful and inappropriate behaviour and the options available to address those behaviours if they experience them or engage in them.</p>
      <p>Well trained Contact Officers provide another resource to assist the organisation to provide a safe and respectful workplace.</p>
    </div>
  </section>

  <svg class="icon-badge" viewBox="0 0 142 142" role="img" aria-label="Icon of a presenter at a board in front of a seated audience">
    <circle cx="71" cy="71" r="71" fill="#ffffff"/>
    <circle cx="71" cy="71" r="59" fill="var(--ring-grey)"/>
    <circle cx="71" cy="71" r="54" fill="var(--band-strong)"/>
  </svg>

  <section class="outcomes">
    <h2>Learning Outcomes</h2>
    <p class="lead">Training will enable participants to perform their role of Contact Officer and to understand:</p>
    <ol>
      <li>1. The role and responsibilities of a Contact Officer.</li>
      <li>2. What amounts to unlawful workplace behaviour.</li>
      <li>3. What is considered inappropriate behaviour in our workplace.</li>
      <li>4. How to apply understanding unlawful/inappropriate behaviour to common scenarios.</li>
      <li>5. How to address and resolve grievances early.</li>
      <li>6. Options to resolve grievances internally and the Contact Officer role.</li>
      <li>7. External options and their pros and cons for resolving grievances.</li>
    </ol>
  </section>

  <aside class="overview">
    <div class="band strong" style="top:0;height:198px;padding-top:36px">
      <h2 class="overview-title">Training Overview</h2>
      <h3>Discrimination</h3>
      <p class="bold">What is direct and indirect discrimination?</p>
      <p>What are the prescribed attributes?</p>
      <p>What are the exceptions to the general rules?</p>
      <p class="ex">Practical examples of behaviour.<br>that may be discriminatory.</p>
    </div>
    <div class="band mid" style="top:198px;height:201px;padding-top:12px">
      <h3>Harassment</h3>
      <p class="bold">What is harassment?</p>
      <p>Are protected attributes relevant to harassment?</p>
      <p>What is the difference between harassment and sexual harassment?</p>
      <p>How does the reasonable person test work in relation to harassment?</p>
      <p class="ex dark">Practical examples of behaviour that may be harassment or sexual harassment.</p>
    </div>
    <div class="band soft" style="top:399px;height:191px;padding-top:8px">
      <h3>Bullying</h3>
      <p class="bold">What is bullying?</p>
      <p>Explore how bullying differs to discrimination or inappropriate behaviour.</p>
      <p>Performance Management - when it will and will not be bullying.</p>
      <p>Is all workplace conflict bullying?</p>
      <p class="ex">Practical examples of behaviour that may be bullying.</p>
    </div>
    <div class="band strong" style="top:590px;height:81px;padding-top:17px">
      <h3>Victimisation &amp; Vilification</h3>
      <p class="bold">What is Victimisation? What is Vilification?</p>
    </div>
    <div class="band mid" style="top:671px;height:182px;padding-top:12px">
      <h3>Adverse Action</h3>
      <p>What is adverse action and how does it differ to other unlawful behaviour?</p>
      <p>What is a workplace right?</p>
      <p>When is it lawful to terminate employment because of an employee’s absence?</p>
      <p>How are the protected attributes relevant to adverse action?</p>
    </div>
    <div class="band soft small" style="top:853px;height:126px;padding-top:10px">
      <h3>The Contact Officer’s role</h3>
      <p>How to perform your role when approached by an employee – the 6 step approach.<br>What not to do.</p>
      <p>What are the obligations with regard to Confidentiality?</p>
    </div>
    <div class="band strong small" style="top:979px;height:150px;padding-top:10px">
      <h3>Grievance Options</h3>
      <p>Explore the options of complaint management - self management, internal informal management, formal internal management.</p>
      <p>How do they compare and what are the advantages and disadvantages of each approach. Is doing nothing an option?</p>
    </div>
    <div class="band mid" style="top:1129px;height:71px;padding-top:14px">
      <h3>Test Learning</h3>
      <p>Role play, group discussion</p>
    </div>
  </aside>

</main>
</body>
</html>
```